Redesign of business card for Cedar Ridge Mechanical

We are looking for a new design for our business cards for Cedar Ridge Mechanical. We are a plumbing & HVAC construction company, operating on the West Coast of Canada and USA. Logo attached.
Industry/Entity Type
Construction - Plumbing & HVAC
Contact Information for Business Card
Name, address, phone numbers, email, website address
Look and feel
Each slider illustrates characteristics of the customer's brand and the style your logo design should communicate.

```html
<!DOCTYPE html>
<html lang="en">
<head>
<meta charset="utf-8">
<title>Cedar Ridge Mechanical – Business Card</title>
<link rel="stylesheet" href="https://fonts.googleapis.com/css2?family=Open+Sans:wght@400;600;700&display=swap">
<style>
  :root {
    --page-bg: #f2efea;
    --card-bg: #e3dcd2;
    --ink-dark: #272220;
    --band-black: #0e0d0c;
    --swoosh-grey: #8d8a86;
    --text-light: #eee5d7;
    --text-soft: #d8cdbb;
  }
  html, body {
    margin: 0;
    padding: 0;
    width: 1200px;
    height: 1047px;
    overflow: hidden;
    background: var(--page-bg);
    font-family: "Open Sans", Arial, sans-serif;
  }
  .business-card {
    position: absolute;
    left: 80px;
    top: 240px;
    width: 1040px;
    height: 566px;
    border-radius: 24px;
    overflow: hidden;
    background: linear-gradient(135deg, #e8e2d9 0%, var(--card-bg) 100%);
    box-shadow: 0 10px 30px rgba(0,0,0,0.12);
  }
  .card-waves {
    position: absolute;
    inset: 0;
    width: 100%;
    height: 100%;
  }
  .brand {
    position: absolute;
    left: 52px;
    top: 150px;
    display: flex;
    align-items: center;
    gap: 18px;
  }
  .brand-square {
    width: 34px;
    height: 34px;
    background: var(--ink-dark);
  }
  .brand-name {
    font-size: 34px;
    font-weight: 700;
    color: var(--ink-dark);
    letter-spacing: 1px;
    text-transform: uppercase;
  }
  .contact-block {
    position: absolute;
    right: 39px;
    text-align: right;
    margin: 0;
  }
  .person-name {
    top: 236px;
    font-size: 32px;
    line-height: 44px;
    font-weight: 700;
    color: var(--text-light);
    letter-spacing: 0.5px;
  }
  .person-title {
    top: 280px;
    font-size: 25px;
    line-height: 34px;
    color: var(--text-soft);
  }
  .address {
    top: 330px;
    font-size: 24px;
    line-height: 36px;
    color: var(--text-soft);
  }
  .contact-list {
    top: 420px;
    list-style: none;
    padding: 0;
    font-size: 23px;
    line-height: 37px;
    color: var(--text-soft);
  }
  .contact-list li {
    display: flex;
    justify-content: flex-end;
    align-items: center;
    gap: 12px;
  }
  .contact-icon {
    width: 22px;
    height: 22px;
    fill: none;
    stroke: var(--text-soft);
    stroke-width: 2;
  }
</style>
</head>
<body>
  <div class="business-card">
    <svg class="card-waves" viewBox="0 0 878 478" preserveAspectRatio="none" aria-hidden="true">
      <path d="M878,140 C780,140 700,160 620,200 C500,265 380,385 0,385 L0,478 L878,478 Z" fill="var(--band-black)"/>
      <path d="M0,352 C250,385 420,290 520,232 C640,160 740,120 878,120" fill="none" stroke="var(--swoosh-grey)" stroke-width="8"/>
      <path d="M0,300 C70,340 140,365 230,380 C140,385 60,380 0,372 Z" fill="var(--band-black)"/>
    </svg>

    <div class="brand">
      <span class="brand-square"></span>
      <span class="brand-name">Cedar Ridge Mechanical</span>
    </div>

    <p class="contact-block person-name">DANIEL HARPER</p>
    <p class="contact-block person-title">Managing Director</p>
    <p class="contact-block address">Your address, City<br>State, Zip 1234</p>

    <ul class="contact-block contact-list">
      <li>123 456 789
        <svg class="contact-icon" viewBox="0 0 24 24"><path d="M5 3 L9 3 L10 8 L7.5 9.5 C9 13 11 15 14.5 16.5 L16 14 L21 15 L21 19 C21 20 20 21 19 21 C10 21 3 14 3 5 C3 4 4 3 5 3 Z"/></svg>
      </li>
      <li>info@yourmail.com
        <svg class="contact-icon" viewBox="0 0 24 24"><rect x="3" y="6" width="18" height="13" rx="1"/><path d="M3 7 L12 14 L21 7"/></svg>
      </li>
      <li>www.yourwebsite.com
        <svg class="contact-icon" viewBox="0 0 24 24"><circle cx="12" cy="12" r="9"/><path d="M3 12 H21 M12 3 C8 8 8 16 12 21 M12 3 C16 8 16 16 12 21"/></svg>
      </li>
    </ul>
  </div>
</body>
</html>
```